Accounting firm needing business card / letterhead designed
Marcus L. Trenholm, CPA
marcus@veltrowledger.com
www.veltrowledger.com
842 E Alder Ave Perrysburg, OH 43827
419-562-0974

```html
<!DOCTYPE html>
<html lang="en">
<head>
<meta charset="utf-8">
<title>Veltrow Ledger — Business Card</title>
<link rel="stylesheet" href="https://fonts.googleapis.com/css2?family=Roboto:wght@400;700&family=Roboto+Condensed:wght@700&display=swap">
<style>
  :root {
    --backdrop: #a7a7a7;
    --brand-green: #8dc63f;
    --brand-navy: #262262;
    --card-white: #f4f4f4;
    --text-gray: #4f4f4f;
    --text-white: #ffffff;
  }
  * { margin: 0; padding: 0; box-sizing: border-box; }
  html, body {
    width: 1200px; height: 960px; overflow: hidden;
    background: var(--backdrop);
    font-family: "Roboto", Arial, sans-serif;
  }
  .stage { position: relative; width: 1200px; height: 960px; }
  .card {
    position: absolute; left: 320px; width: 600px; height: 340px;
    border-radius: 22px; overflow: hidden;
  }
  .card--front { top: 108px; background: var(--brand-green); }
  .card--back { top: 494px; background: var(--card-white); }

  .front-wordmark {
    position: absolute; top: 114px; left: 0; width: 100%;
    text-align: center;
    font-weight: 700; font-size: 52px; letter-spacing: 3px;
    color: var(--brand-navy);
  }
  .front-website {
    position: absolute; top: 280px; left: 0; width: 100%;
    text-align: center; color: var(--text-white);
    font-size: 14px; letter-spacing: 5.5px;
  }

  .back-wordmark {
    position: absolute; left: 38px; top: 50px;
    font-weight: 700; font-size: 27px; letter-spacing: 1px;
    line-height: 36px;
    color: var(--brand-navy); white-space: nowrap;
  }
  .name-band { position: absolute; left: 0; top: 38px; width: 600px; height: 56px; }
  .name-band__text {
    position: absolute; left: 330px; top: 38px; height: 56px; width: 270px;
    display: flex; align-items: center; justify-content: center;
    font-family: "Roboto Condensed", "Arial Narrow", sans-serif;
    font-weight: 700; font-size: 21px; color: var(--text-white); white-space: nowrap;
  }
  .address {
    position: absolute; left: 35px; top: 209px;
    font-size: 14px; line-height: 19px; color: var(--text-gray); font-style: normal;
  }
  .contacts {
    position: absolute; left: 36px; top: 256px; list-style: none;
    font-size: 14px; line-height: 19px; color: var(--text-gray);
  }
  .contacts li { display: flex; align-items: center; gap: 8px; }
  .contacts svg { width: 14px; height: 14px; fill: var(--brand-navy); flex: none; }
</style>
</head>
<body>
<main class="stage">
  <section class="card card--front" aria-label="Card front">
    <div class="front-wordmark">VELTROW LEDGER</div>
    <div class="front-website">www.veltrowledger.com</div>
  </section>

  <section class="card card--back" aria-label="Card back">
    <div class="back-wordmark">VELTROW LEDGER</div>
    <svg class="name-band" viewBox="0 0 600 56" aria-hidden="true">
      <polygon points="345,0 600,0 600,56 322,56" fill="var(--brand-navy)"/>
    </svg>
    <div class="name-band__text">Marcus L. Trenholm, CPA</div>

    <address class="address">
      842 E Alder Ave<br>Perrysburg, OH 43827
    </address>
    <ul class="contacts">
      <li>
        <svg viewBox="0 0 24 24"><path d="M6.6 10.8a15.1 15.1 0 0 0 6.6 6.6l2.2-2.2a1 1 0 0 1 1-.25 11.4 11.4 0 0 0 3.6.57 1 1 0 0 1 1 1V20a1 1 0 0 1-1 1A17 17 0 0 1 3 4a1 1 0 0 1 1-1h3.5a1 1 0 0 1 1 1c0 1.25.2 2.45.57 3.570a1 1 0 0 1-.25 1z"/></svg>
        419-562-0974
      </li>
      <li>
        <svg viewBox="0 0 24 24"><path d="M2 5h20v14H2z M3.5 6.5 12 12.5l8.5-6z" fill-rule="evenodd"/></svg>
        marcus@veltrowledger.com
      </li>
      <li>
        <svg viewBox="0 0 24 24"><circle cx="12" cy="12" r="10"/><path d="M7 8c2 0 3 1 3 3s-2 2-2 4M14 5c0 2 2 3 3 3M13 19c0-2 2-3 4-3" stroke="#f4f4f4" stroke-width="1.6" fill="none"/></svg>
        www.veltrowledger.com
      </li>
    </ul>
  </section>
</main>
</body>
</html>
```